Church Website with Home Page and Member Sermon Library

I am in need of an updated design for our church website. This will include 4 pages (outlined below). We are a conservative, evangelical, Christian church. The site should be modern and clean, while still reflecting our conservative values. I already have a logo for our church, and I want the site to incorporate the logo, and match the logo/branding. Stock photos are allowed if needed, but I have uploaded some images of our church and would prefer those images to be used if possible. Any stock photos used should not include any people in the photos (scenery, nature, buildings, animals, etc. are fine).

The site will need 4 pages: Home, Support Us (Donate), Login, and Recording Library.

Page 1: Home
The home page should include the following sections:

- Navigation: Should include links to each section of the home page plus a "listen live" link which will take the user to a live-streaming site and a "support us" link which will take the user to a support/donate page.

- Announcements: Can be either a banner or some other design, but there needs to be some way for us to post announcements for visitors to see. I'm open for creative ideas in this section, but would like it not to take up a lot of room on the page.

- About Us: Should include address, service times (see attached document), and information about the church.

- Pastor Bio: A section that introduces our pastor and gives a short bio about our pastor. Would like this section to include a picture of our pastor. Somewhere in this section I would like to include this Bible reference: "And I will give you pastors according to mine heart, which shall feed you with knowledge and understanding. Jer 3:15 LPW"

- Articles of Faith (What We Believe): This should include several sub-sections each with a heading, body, and possibly 1 or more scripture references. I have attached a document to the brief that includes our articles of faith. Feel free to be creative with this section in how you lay these out and format them.

- Support Us: A small section that explains what kind of support someone can give and a link to a donation page. The link can say something like "Support Us" or "Donate Now".

- Contact form: A contact form that allows the visitor to send us a message. The contact form should ask for name, email, phone, and message.

- Footer: A footer that will be displayed on all pages of the site. This should include at a minimum a link to the home page (or a link to each individual section in the home page if you prefer), a link to "listen live", a link to "support us", a link to "contact us" (or you can put the contact form directly in the footer if you prefer), the address, and a "member login" link.

Page 2: Support Us
The donation page should include a form the visitor can fill out to make a donation. We will embed a third party form later. For this design, please just mock out the design with a basic form asking for name, phone, and email.

Page 3: Login
The recording library (detailed below) will require members to login with a shared numeric code before accessing the page. We need a design for a login screen. The screen should include navigation/footer just like all other pages, but the body of the login page will consist only of a form that asks the user to enter the access code and then a "login" button.

Page 4: Recording Library

The library page is a member-only page that will require a shared, numeric pass code to access. On this page, members will be able to access a filterable list of past sermons. The page by default should display most recent sermons, but should also include a search form that allows the member to filter the sermon list to find a particular sermon. The search form should allow the user to select a filter type (e.g. Speaker name, date, event, etc.) and type in a value to search. They should be able to add multiple filters and remove filters that have been added. Each sermon that is displayed in the result list should include basic information such as title, date, speaker, tags, etc. along with a download icon, and an embedded audio player where they can click a play button to stream it on-demand. Each sermon should also have clickable tags associated with it that can be used to find related sermons.
Updates

I have uploaded several images of our church. Feel free to incorporate these into your design if possible.

Target Market(s)

Church Members

Industry/Entity Type

Religion

Number of Pages Required

4 page

Font styles to use
Sans Serif

Colors

Designer to choose colors to be used in the design.

Requirements
Must have
• Must incorporate the logo (attached)
Nice to have
• Would like the design to incorporate pictures of our church (attached) instead of stock photos if possible.
Should not have
• Please avoid an overly cluttered design. Stock photos used should not include any people in the photos.

```html
<!DOCTYPE html>
<html lang="en">
<head>
<meta charset="utf-8">
<title>Grace Hill Chapel</title>
<link href="https://fonts.googleapis.com/css2?family=Inter:wght@400;500;600;700;900&family=Marcellus&display=swap" rel="stylesheet">
<style>
:root{
  --cream:#f7f2ea;
  --green:#658c4c;
  --green-light:#87ab72;
  --green-dark:#2d4a18;
  --ink:#141414;
  --teal:#1590a8;
  --dark:#262626;
  --white:#ffffff;
}
*{margin:0;padding:0;box-sizing:border-box}
html,body{width:1200px;height:3079px;overflow:hidden}
body{background:var(--cream);font-family:"Inter",sans-serif;color:var(--ink);position:relative}
.abs{position:absolute}
.serif{font-family:"Marcellus",serif;font-weight:400}
.btn{position:absolute;display:flex;align-items:center;justify-content:center;gap:8px;font-size:13px;font-weight:500;border-radius:2px;text-decoration:none}
.btn-dark{background:var(--green-dark);color:var(--white)}
.btn-light{background:var(--white);color:var(--green-dark)}
.chev{width:8px;height:8px}

/* pastor */
.pastor-text{left:195px;top:-2px;width:350px;font-size:15px;line-height:21px}
.pastor-text p+p{margin-top:21px}
.pastor-photo{left:598px;top:-20px;width:407px;height:328px;border-radius:0 0 30px 30px;background:linear-gradient(160deg,#8a7a62 0%,#a76f35 45%,#5a4630 100%);border-right:6px solid var(--teal);border-bottom:6px solid var(--teal)}

/* beliefs */
.beliefs-bg{left:0;top:0}
.kicker{left:0;width:1200px;top:600px;text-align:center;font-size:11px;letter-spacing:3px;color:var(--white)}
.beliefs-title{left:0;width:1200px;top:630px;text-align:center;font-size:39px;color:var(--white)}
.card-img{top:701px;width:260px;height:237px;border-radius:10px}
.card{top:957px;width:260px;color:var(--white)}
.card .tag{font-size:10px;font-weight:700;letter-spacing:.3px}
.card h3{font-size:19px;font-weight:600;margin-top:8px}
.card p{font-size:11px;line-height:17.5px;margin-top:16px;opacity:.92}
.card .more{position:absolute;top:141px;font-size:10px;font-weight:700;display:flex;align-items:center;gap:6px}

/* support */
.section-title{left:0;width:1200px;text-align:center;font-size:32px;color:var(--ink)}
.support-copy{left:225px;width:750px;top:1461px;text-align:center;font-size:15.5px;line-height:25px}
.rule{height:3px;background:linear-gradient(90deg,rgba(21,144,168,0),var(--teal) 40%,var(--teal) 60%,rgba(21,144,168,0))}

/* banner */
.banner{left:195px;top:1819px;width:809px;height:211px;border-radius:106px;border:1px solid #d8c49a;background:#f7f6f4;overflow:hidden}
.banner .mark{left:22px;top:88px;width:34px;height:34px;border:1.5px solid #555;border-radius:50%}
.banner .mark-name{left:62px;top:70px;font-size:9px;font-weight:600;letter-spacing:2px;writing-mode:vertical-rl;transform:rotate(180deg);color:#444}
.banner h2{left:98px;top:32px;font-size:44px;line-height:44px;font-weight:900;color:#111}
.banner .time{left:96px;top:122px;font-size:32px;font-weight:700;color:var(--green)}
.banner .sub{left:98px;top:161px;font-size:19px;color:#222}
.banner .art{left:330px;top:0;width:479px;height:211px;background:linear-gradient(100deg,#f7f6f4 0%,#ee7a22 22%,#f6a31a 55%,#f7f6f4 90%)}

/* footer */
.footer{left:0;top:2071px;width:1200px;height:1008px;background:var(--dark)}
.footer-notch{left:0;top:2070px}
.contact-title{left:0;width:1200px;top:2196px;text-align:center;font-size:38px;color:var(--white)}
.form{left:326px;top:2282px;width:540px;height:396px;background:var(--green-light);border-radius:16px}
.field{position:absolute;font-size:12.5px;color:var(--white)}
.field .line{position:absolute;left:0;height:1px;background:rgba(255,255,255,.75)}
.field .ph{position:absolute;left:0;display:flex;align-items:center;gap:7px;font-size:10.5px;color:rgba(255,255,255,.8)}
.brand{left:0;width:1200px;top:2718px;display:flex;flex-direction:column;align-items:center;gap:14px;color:var(--white)}
.brand .sq{width:30px;height:30px;border:1.5px solid var(--white)}
.brand .name{font-size:22px;font-weight:500;letter-spacing:4px}
.footer-nav{left:0;width:1200px;top:2866px;display:flex;justify-content:center;gap:29px;font-size:11.5px;color:#cfcfcf}
.address{left:0;width:1200px;top:2941px;text-align:center;font-size:11px;color:var(--white)}
.socials{left:0;width:1200px;top:2974px;display:flex;justify-content:center;gap:11px}
.socials span{width:33px;height:33px;border-radius:50%;background:var(--teal)}
.copy{left:0;width:1200px;top:3027px;text-align:center;font-size:11px;font-weight:600;color:var(--white)}
</style>
</head>
<body>

<!-- pastor -->
<div class="abs pastor-text">
  <p>make a type specimen book. It has survived not only five centuries, but also the leap into electronic typesetting, remaining essentially unchanged.</p>
  <p>Bible reference: “And I will give you pastors according to mine heart, which shall feed you with knowledge and understanding.”</p>
</div>
<a class="btn btn-dark" style="left:195px;top:200px;width:118px;height:39px">Book a Visit <svg class="chev" viewBox="0 0 8 8"><path d="M2.5 1 5.5 4 2.5 7" fill="none" stroke="currentColor" stroke-width="1.4"/></svg></a>
<div class="abs pastor-photo" role="img" aria-label="Church member seated in a wooden pew"></div>

<!-- beliefs -->
<svg class="abs beliefs-bg" width="1200" height="1360" viewBox="0 0 1200 1360">
  <path d="M44,568 Q44,468 144,468 L600,492 L1056,468 Q1156,468 1156,568 L1156,1244 Q1156,1344 1056,1344 L600,1320 L144,1344 Q44,1344 44,1244 Z" fill="#658c4c"/>
</svg>
<div class="abs kicker serif">ARTICLES OF FAITH</div>
<h2 class="abs beliefs-title serif">What We Believe</h2>

<div class="abs card-img" style="left:195px;background:linear-gradient(180deg,#d9d7d4 0%,#cfc9c2 45%,#a58a6c 60%,#d7c3a6 100%)" role="img" aria-label="Brick church building under an overcast sky"></div>
<div class="abs card-img" style="left:470px;background:linear-gradient(180deg,#6a7a88 0%,#c29a6e 50%,#b9c4cc 100%)" role="img" aria-label="Cathedral nave with rows of wooden chairs"></div>
<div class="abs card-img" style="left:745px;background:linear-gradient(180deg,#c8ccd4 0%,#9aa2b0 50%,#6e5a46 100%)" role="img" aria-label="Church interior with pillars and wooden pews"></div>

<div class="abs card" style="left:204px">
  <div class="tag">EVENTS</div><h3>The God Head</h3>
  <p>We believe in the God head bodily, known as the Divine Trinity. This body consist of God the father, Jesus Christ, his only begotten son and the.</p>
  <div class="more">Know More <svg class="chev" viewBox="0 0 8 8"><path d="M2.5 1 5.5 4 2.5 7" fill="none" stroke="#fff" stroke-width="1.4"/></svg></div>
</div>
<div class="abs card" style="left:470px">
  <div class="tag">EVENTS</div><h3>Full Salvation.</h3>
  <p>We believe that Salvation is received only when a person comes to the realization that he or she is lost and separated from God and becomes full of godly sorrow.</p>
  <div class="more">Know More <svg class="chev" viewBox="0 0 8 8"><path d="M2.5 1 5.5 4 2.5 7" fill="none" stroke="#fff" stroke-width="1.4"/></svg></div>
</div>
<div class="abs card" style="left:745px">
  <div class="tag">EVENTS</div><h3>Sanctification.</h3>
  <p>Printer took a galley of type and scrambled it to make a type specimen book. It has survived not only five centuries, but also the leap into.</p>
  <div class="more">Know More <svg class="chev" viewBox="0 0 8 8"><path d="M2.5 1 5.5 4 2.5 7" fill="none" stroke="#fff" stroke-width="1.4"/></svg></div>
</div>
<a class="btn btn-light" style="left:536px;top:1176px;width:127px;height:39px">Explore More <svg class="chev" viewBox="0 0 8 8"><path d="M2.5 1 5.5 4 2.5 7" fill="none" stroke="currentColor" stroke-width="1.4"/></svg></a>

<!-- support -->
<h2 class="abs section-title serif" style="top:1393px">Support Our Church</h2>
<p class="abs support-copy">Christian Refugees in crisis. We are raising funds for thesesurvivors who are facing cold winter weather without shelter, clothes,blankets, food &amp; water. People are sleeping outside anywhere they can find a somewhat safe spot.</p>
<a class="btn btn-dark" style="left:542px;top:1561px;width:116px;height:39px">Support Us <svg class="chev" viewBox="0 0 8 8"><path d="M2.5 1 5.5 4 2.5 7" fill="none" stroke="currentColor" stroke-width="1.4"/></svg></a>
<div class="abs rule" style="left:195px;top:1643px;width:810px"></div>

<!-- announcement -->
<h2 class="abs section-title serif" style="top:1712px;font-size:37px">Important Announcement</h2>
<div class="abs banner">
  <div class="abs mark"></div>
  <div class="abs mark-name">GRACE HILL</div>
  <h2 class="abs">WORSHIP<br>WITH US</h2>
  <div class="abs time">11 PM</div>
  <div class="abs sub">Watch us live &amp; enjoy</div>
  <div class="abs art" role="img" aria-label="Service time announcement graphic with a megaphone"></div>
</div>

<!-- footer -->
<div class="abs footer"></div>
<svg class="abs footer-notch" width="1200" height="42" viewBox="0 0 1200 42"><path d="M0,0 L1200,0 L1200,1 L614,39 L0,1 Z" fill="#f7f2ea"/></svg>
<h2 class="abs contact-title serif">Get In Touch With Us</h2>
<form class="abs form">
  <div class="field" style="left:53px;top:52px">First Name
    <div class="line" style="top:46px;width:199px"></div>
    <div class="ph" style="top:25px;width:1px;height:16px;background:#fff"></div>
  </div>
  <div class="field" style="left:288px;top:52px">Last Name
    <div class="line" style="top:46px;width:200px;left:3px"></div>
    <div class="ph" style="top:27px;left:3px"><svg width="10" height="10" viewBox="0 0 10 10"><circle cx="5" cy="3" r="2" fill="none" stroke="#fff"/><path d="M1 9.5C1 7 3 6 5 6s4 1 4 3.5" fill="none" stroke="#fff"/></svg>Smith</div>
  </div>
  <div class="field" style="left:53px;top:133px">Contact Number
    <div class="line" style="top:47px;width:199px"></div>
    <div class="ph" style="top:26px"><svg width="10" height="10" viewBox="0 0 10 10"><path d="M2 1l2 2-1 1.5c.7 1.3 1.3 1.9 2.5 2.5L7 6l2 2-1.5 1.5C4 9 1 6 .5 2.5Z" fill="#fff"/></svg>+1-095-568-098</div>
  </div>
  <div class="field" style="left:290px;top:133px">Email Address
    <div class="line" style="top:47px;width:199px"></div>
    <div class="ph" style="top:27px"><svg width="11" height="9" viewBox="0 0 11 9"><rect x=".5" y=".5" width="10" height="8" fill="none" stroke="#fff"/><path d="M.5 .5 5.5 5 10.5 .5" fill="none" stroke="#fff"/></svg>john@gmail.com</div>
  </div>
  <div class="field" style="left:53px;top:215px">Message
    <div class="line" style="top:67px;width:435px"></div>
    <div class="ph" style="top:24px;left:2px"><svg width="10" height="10" viewBox="0 0 10 10"><path d="M1 9l1-3 5-5 2 2-5 5Z" fill="#fff"/></svg>Hello...</div>
  </div>
  <a class="btn btn-dark" style="left:200px;top:321px;width:148px;height:39px">Submit Message <svg class="chev" viewBox="0 0 8 8"><path d="M2.5 1 5.5 4 2.5 7" fill="none" stroke="currentColor" stroke-width="1.4"/></svg></a>
</form>

<div class="abs brand"><div class="sq"></div><div class="name">GRACE HILL CHAPEL</div></div>
<nav class="abs footer-nav"><span>Home</span><span>About</span><span>Pastor</span><span>Listen Live</span><span>Library</span><span>Donation</span><span>Support Us</span><span>Member Login</span></nav>
<div class="abs rule" style="left:195px;top:2916px;width:810px"></div>
<div class="abs address">218 Maple Ridge Lane, Brookhaven, Ohio 44021</div>
<div class="abs socials"><span></span><span></span><span></span><span></span></div>
<div class="abs copy">© Copyright Grace Hill Chapel 2023. All Right Reserved.</div>
</body>
</html>
```